Webdesign für Reittherapeutin
Zielgruppe
Ich bin Reittherapeutin und biete auf unserem privaten Hof Reittherapie für Kinder, Jugendliche und Erwachsene an. Die Therapieeinheiten finden im Freien statt, also auf dem Sandplatz oder im Gelände. In der Reittherapie steht nicht das Reiten, sonden der Umgang und die Beziehung zum Pferd im Vordergrund.
Aufgabenstellung
Mir gefallen Designs in Naturtönen, welche auch gut zu meiner Tätigkeit passen. Ich habe bereits ein Logo, einen Namen (Wiesen erleben) und die Domaine (www.wiesen-erleben.ch) ebenso.

```html
<!DOCTYPE html>
<html lang="de">
<head>
<meta charset="utf-8">
<title>Kontakt – Wiesen erleben</title>
<link rel="stylesheet" href="https://fonts.googleapis.com/css2?family=Poppins:wght@300;400;500;600;800&family=Quicksand:wght@400;500;700&display=swap">
<style>
  :root {
    --canvas: #efeeec;
    --headline: #777777;
    --brown: #6f5a4e;
    --nav-bg: #fdfaf8;
    --body-bg: #fcf8f5;
    --footer-bg: #ffffff;
    --text: #5d5d5d;
    --muted: #9a9694;
    --line: #b5b0ad;
    --photo-a: #6f5f58;
    --photo-b: #b9ad9a;
    --map-a: #ecebea;
    --map-b: #e2e4e6;
  }
  * { margin: 0; padding: 0; box-sizing: border-box; }
  html, body { width: 1200px; height: 2564px; overflow: hidden; }
  body {
    position: relative;
    background: var(--canvas);
    font-family: "Poppins", sans-serif;
    color: var(--text);
  }
  .board-title, .board-closing {
    position: absolute; left: 0; width: 1200px;
    text-align: center; font-weight: 800; color: var(--headline);
    font-size: 58px; line-height: 86px; letter-spacing: -0.5px;
  }
  .board-title { top: 332px; }
  .board-closing { top: 2290px; }
  .board-label {
    position: absolute; top: 910px; left: 0; width: 1200px;
    text-align: center; font-size: 68px; font-weight: 500; color: var(--brown);
  }
  .site-window {
    position: absolute; left: 118px; top: 1092px; width: 964px; height: 981px;
    border-radius: 6px; overflow: hidden; background: var(--body-bg);
    box-shadow: 0 10px 40px rgba(0,0,0,0.10);
  }
  .site-nav {
    position: absolute; left: 0; top: 0; width: 100%; height: 94px; background: var(--nav-bg);
  }
  .brand {
    position: absolute; left: 98px; top: 28px; display: flex; align-items: center; gap: 8px;
    font-size: 16px; font-weight: 500; color: var(--brown);
  }
  .brand-dot { width: 40px; height: 40px; border-radius: 50%; background: var(--brown); }
  .nav-links { position: absolute; top: 43px; left: 0; font-size: 13px; color: var(--text); }
  .nav-links span { position: absolute; white-space: nowrap; }
  .nav-links .active { font-weight: 600; color: var(--brown); }
  .nav-links .active::after {
    content: ""; position: absolute; left: -6px; right: -6px; top: 24px; height: 3px; background: var(--brown);
  }
  .hero-photo {
    position: absolute; left: 0; top: 94px; width: 100%; height: 341px;
    background: linear-gradient(90deg, var(--photo-a) 0%, #8a7c74 40%, var(--photo-b) 70%, #a49a8b 100%);
  }
  .contact-title {
    position: absolute; top: 448px; width: 100%; text-align: center;
    font-family: "Quicksand", sans-serif;
    font-size: 30px; font-weight: 700; color: var(--brown);
  }
  .contact-intro {
    position: absolute; top: 497px; width: 100%; text-align: center;
    font-family: "Quicksand", sans-serif;
    font-size: 13px; line-height: 17px; font-weight: 500; color: #444; letter-spacing: 0.3px;
  }
  .field {
    position: absolute; left: 98px; width: 376px;
    font-family: "Quicksand", sans-serif;
    font-size: 15px; color: #555; font-weight: 500;
  }
  .field-line { border-bottom: 1px solid var(--line); height: 26px; padding-left: 10px; }
  .field-area { border: 1px solid var(--line); height: 156px; padding: 10px 7px; }
  .send-button {
    position: absolute; left: 98px; top: 836px; width: 112px; height: 31px;
    background: var(--brown); color: #fff; border-radius: 5px;
    font-size: 11px; text-align: center; line-height: 31px;
  }
  .map-area {
    position: absolute; left: 493px; top: 569px; width: 376px; height: 184px;
    background: linear-gradient(180deg, var(--map-a) 0%, var(--map-b) 100%);
  }
  .address, .reach {
    position: absolute; top: 770px; font-size: 14px; line-height: 23px; font-weight: 300; color: var(--muted);
  }
  .address { left: 494px; }
  .reach { left: 668px; line-height: 33px; }
  .site-footer {
    position: absolute; left: 0; top: 920px; width: 100%; height: 61px; background: var(--footer-bg);
    font-size: 10px; color: #555;
  }
  .site-footer span { position: absolute; top: 24px; white-space: nowrap; }
</style>
</head>
<body>
  <h1 class="board-title">Fortsetzung für das letzte Design<br>(Die Kontakt Seite)</h1>
  <div class="board-label">Kontakt</div>

  <div class="site-window">
    <header class="site-nav">
      <div class="brand"><span class="brand-dot"></span>Wiesen erleben</div>
      <nav class="nav-links">
        <span style="left:475px">Angebot</span>
        <span style="left:556px">Reittherapie</span>
        <span style="left:660px">Über mich</span>
        <span style="left:747px">Pferde</span>
        <span class="active" style="left:817px">Kontakt</span>
      </nav>
    </header>

    <div class="hero-photo" role="img" aria-label="Foto: Reiterin mit Helm steht Stirn an Stirn mit einem Pferd auf dem Sandplatz"></div>

    <h2 class="contact-title">Kontakt</h2>
    <p class="contact-intro">Kontaktieren Sie mich jetzt, um alles weiter zu besprechen,<br>ich freue mich auf Ihnen!</p>

    <div class="field field-line" style="top:573px">Vor -und Zuname</div>
    <div class="field field-line" style="top:623px">Email Adresse</div>
    <div class="field field-area" style="top:666px">Deine Nachricht</div>
    <div class="send-button">Senden</div>

    <div class="map-area" role="img" aria-label="Karte mit dem Standort des Hofes"></div>

    <div class="address">Lea Brunner<br>Mattenweg 4<br>8400 Wiesental</div>
    <div class="reach">info@wiesen-erleben.ch<br>+41 79 000 12 34</div>

    <footer class="site-footer">
      <span style="left:98px">© 2020 Wiesen erleben All Rights Reserved</span>
      <span style="left:664px">Datenschutz</span>
      <span style="left:762px">AGB</span>
      <span style="left:814px">Impressum</span>
    </footer>
  </div>

  <p class="board-closing">Ich hoffe das mein Design<br>Ihn gefallen hat :)</p>
</body>
</html>
```